Stage Design Company Business Card

We are looking to step up up our business card design for our team.

We are a Full service Design and Consultation company for Stage and TV with an emphasis in Theatrical Lighting.

We like our materials to be clean and modern with solid colors free of patterns and gradients. Our brand consists of 4 primary colors Purple, Black, Grey, and White. Provided is our Word Mark as well as our Symbol Logo.

We would like our cards to leave an impression beyond the information, show our attention to design and detail, and make our marks an easily recognized feature (together or apart) for our clients.

We need a warm approachable comfortable feel for some clients, and a professional flair for the board member type clients.

Attached are our brand elements, and our existing cards to give a sense of our style and a glipse at the information we provide on our cards.

Target Market(s)

broad client base from church leaders to high school teachers and architects.

Industry/Entity Type

Business

Contact Information for Business Card

We format our phone number with periods not parenthesis or dashes. Information will be edited for each of our team members, and team member specific cards are not part of this scope, but rather a template so to speak.

Font styles to use
Sans Serif

Colors
6b449b
ffffff
000000
333333
aaaaaa

Requirements
Must have
• Wordmark and logo mark present (does not need to exist on the same side of card)
• Brand Colors,
• Name, Phone, Email, Address.
• Unique choices that make someone stop and take a second look
Nice to have
• It would be nice to somehow convey what we DO, as our brand name does not lend itself to this, outside of an obvious tagline though.....
• social media if not crowded. all of our handles match (instagram, twitter, facebook)
Should not have
• "clipart"

```html
<!DOCTYPE html>
<html lang="en">
<head>
<meta charset="utf-8">
<title>Halvern Entertainment – Business Card</title>
<link href="https://fonts.googleapis.com/css2?family=Jost:wght@400;500;600&display=swap" rel="stylesheet">
<style>
  :root {
    --backdrop: #8d8c8d;
    --card-purple: #38216a;
    --ink-white: #ffffff;
    --ink-soft: #c9c2dc;
    --card-shadow: rgba(0, 0, 0, 0.28);
  }
  * { margin: 0; padding: 0; box-sizing: border-box; }
  html, body {
    width: 1200px;
    height: 929px;
    overflow: hidden;
    background: var(--backdrop);
    font-family: "Jost", "Futura", sans-serif;
    color: var(--ink-white);
  }
  .canvas { position: relative; width: 1200px; height: 929px; }
  .card {
    position: absolute;
    width: 560px;
    height: 320px;
    background: var(--card-purple);
    box-shadow: 0 6px 14px var(--card-shadow);
  }
  .card--front { left: 120px; top: 110px; }
  .card--back { left: 520px; top: 500px; }

  /* Front */
  .brand {
    position: absolute;
    left: 0; right: 0; top: 0; bottom: 0;
    display: flex;
    align-items: center;
    justify-content: center;
    gap: 12px;
  }
  .brand__dot {
    width: 14px; height: 14px;
    border-radius: 50%;
    background: var(--ink-white);
  }
  .brand__name {
    font-size: 24px;
    font-weight: 500;
    letter-spacing: 6px;
    text-transform: uppercase;
  }

  /* Back */
  .identity {
    position: absolute;
    left: 140px; top: 110px;
    display: flex;
    align-items: center;
  }
  .person { text-align: right; padding-right: 18px; }
  .person__name {
    font-size: 22px;
    font-weight: 600;
    letter-spacing: 0.5px;
    line-height: 1.1;
  }
  .person__role { font-size: 15px; font-weight: 400; }
  .divider { width: 1.5px; height: 52px; background: var(--ink-white); }
  .contacts { list-style: none; padding-left: 16px; font-size: 14px; line-height: 19px; }
  .contacts li { display: flex; align-items: center; gap: 8px; }
  .contacts svg { width: 10px; height: 10px; fill: var(--ink-white); flex: none; }
  .address {
    position: absolute;
    left: 0; right: 0; top: 200px;
    text-align: center;
    font-size: 14px;
    letter-spacing: 0.3px;
  }
  .address svg { display: block; margin: 0 auto 10px; width: 11px; height: 15px; fill: var(--ink-white); }
</style>
</head>
<body>
<main class="canvas">
  <section class="card card--front" aria-label="Card front">
    <div class="brand">
      <span class="brand__dot"></span>
      <span class="brand__name">Halvern Entertainment</span>
    </div>
  </section>

  <section class="card card--back" aria-label="Card back">
    <div class="identity">
      <div class="person">
        <p class="person__name">MARC T HALVERN</p>
        <p class="person__role">Owner</p>
      </div>
      <span class="divider"></span>
      <ul class="contacts">
        <li><svg viewBox="0 0 10 10"><path d="M3 0h4a1 1 0 0 1 1 1v8a1 1 0 0 1-1 1H3a1 1 0 0 1-1-1V1a1 1 0 0 1 1-1zm0 1.5v6h4v-6z"/></svg>800.555.0142</li>
        <li><svg viewBox="0 0 10 10"><path d="M0 2h10v6H0zM0 2l5 3.5L10 2v1L5 6.5 0 3z"/></svg>info@halvern-e.com</li>
        <li><svg viewBox="0 0 10 10"><path d="M4 0a4 4 0 1 1 0 8a4 4 0 0 1 0-8zm0 1.6a2.4 2.4 0 1 0 0 4.8a2.4 2.4 0 0 0 0-4.8zM6.3 7.3l1-1L10 9l-1 1z"/></svg>halvern-e.com</li>
      </ul>
    </div>
    <p class="address">
      <svg viewBox="0 0 11 15"><path d="M5.5 0A5.5 5.5 0 0 1 11 5.5C11 9.5 5.5 15 5.5 15S0 9.5 0 5.5A5.5 5.5 0 0 1 5.5 0zm0 3.3a2.2 2.2 0 1 0 0 4.4a2.2 2.2 0 0 0 0-4.4z"/></svg>
      52 N. Grove ST Alton, AZ 85390
    </p>
  </section>
</main>
</body>
</html>
```